Tall Fern Roofing Business Card

Need a business card with the logo that was designed here

Contact Information for Business Card

Name, Title, Phone, Email, Website, Company name

```html
<!DOCTYPE html>
<html lang="en">
<head>
<meta charset="utf-8">
<title>Tall Fern Roofing Business Card</title>
<link href="https://fonts.googleapis.com/css2?family=Open+Sans:wght@400;600;700&display=swap" rel="stylesheet">
<style>
  :root {
    --stage: #232323;
    --card-dark: #212125;
    --brand-blue: #1a78c8;
    --blue-light: #1f86d6;
    --blue-deep: #0f63ad;
    --band-navy: #2a3442;
    --text-light: #ffffff;
    --text-grey: #a7a9ac;
  }
  * { box-sizing: border-box; margin: 0; padding: 0; }
  html, body { width: 1200px; height: 780px; overflow: hidden; }
  body {
    background: var(--stage);
    font-family: "Open Sans", Arial, sans-serif;
    position: relative;
  }
  .card {
    position: absolute;
    top: 233px;
    width: 550px;
    height: 314px;
    border-radius: 4px;
    overflow: hidden;
    box-shadow: 0 14px 30px rgba(0,0,0,.55);
  }
  .card-front { left: 30px; }
  .card-back { left: 620px; background: var(--card-dark); }

  .front-pattern {
    position: absolute; inset: 0;
    background: linear-gradient(160deg, var(--blue-light) 0%, var(--brand-blue) 55%, var(--blue-deep) 100%);
  }
  .front-name {
    position: absolute; inset: 0;
    display: flex; align-items: center; justify-content: center;
    font-weight: 700; font-size: 38px; letter-spacing: 1px;
    color: #5fa9e3;
  }

  .back-name {
    position: absolute; left: 40px; top: 138px;
    font-weight: 700; font-size: 26px;
    color: var(--brand-blue);
  }
  .divider {
    position: absolute; left: 268px; top: 62px;
    width: 2px; height: 182px; background: var(--text-light);
  }
  .contact { position: absolute; left: 296px; top: 58px; color: var(--text-light); }
  .person-name { font-weight: 700; font-size: 30px; line-height: 1.05; }
  .person-name .first { color: var(--brand-blue); }
  .person-name .last { color: var(--text-grey); }
  .person-title { font-weight: 700; font-size: 13px; margin-top: 4px; }
  .address { font-size: 12.5px; line-height: 1.4; margin-top: 16px; }
  .links { list-style: none; margin-top: 14px; font-size: 12.5px; line-height: 1.6; }
  .links li { display: flex; align-items: center; gap: 8px; }
  .links svg { width: 12px; height: 12px; flex: none; }
  .bottom-band {
    position: absolute; left: 0; right: 0; bottom: 0; height: 10px;
    background: var(--band-navy);
    border-bottom: 4px solid var(--brand-blue);
  }
</style>
</head>
<body>
  <section class="card card-front">
    <div class="front-pattern" role="img" aria-label="Blue background with repeating rows of small house rooftop pattern"></div>
    <div class="front-name">Tall Fern Roofing</div>
  </section>

  <section class="card card-back">
    <div class="back-name">Tall Fern Roofing</div>
    <div class="divider"></div>
    <div class="contact">
      <h1 class="person-name"><span class="first">Dale</span> <span class="last">Morrow</span></h1>
      <p class="person-title">Managing Director</p>
      <p class="address">418 Cedar Ridge Rd. Suite 110<br>Granbury, TX 76048</p>
      <ul class="links">
        <li>
          <svg viewBox="0 0 24 24" aria-hidden="true"><path fill="#1a78c8" d="M6.6 10.8a15 15 0 0 0 6.6 6.6l2.2-2.2a1 1 0 0 1 1-.25 11.4 11.4 0 0 0 3.6.57 1 1 0 0 1 1 1V20a1 1 0 0 1-1 1A17 17 0 0 1 3 4a1 1 0 0 1 1-1h3.5a1 1 0 0 1 1 1c0 1.25.2 2.45.57 3.57a1 1 0 0 1-.25 1z"/></svg>
          (555) 214-6630
        </li>
        <li>
          <svg viewBox="0 0 24 24" aria-hidden="true"><rect x="2" y="5" width="20" height="14" rx="1" fill="none" stroke="#1a78c8" stroke-width="2"/><path d="M2 6l10 7 10-7" fill="none" stroke="#1a78c8" stroke-width="2"/></svg>
          info@website.com
        </li>
        <li>
          <svg viewBox="0 0 24 24" aria-hidden="true"><circle cx="12" cy="12" r="9" fill="none" stroke="#1a78c8" stroke-width="2"/><path d="M3 12h18M12 3c3 3 3 15 0 18M12 3c-3 3-3 15 0 18" fill="none" stroke="#1a78c8" stroke-width="1.6"/></svg>
          www.website.com
        </li>
      </ul>
    </div>
    <div class="bottom-band"></div>
  </section>
</body>
</html>
```